Give Gold Kite an Online Presence!

Gold Kite Property Maintenance is an Australian Owned property maintenance company who needs a stand out online presence.

GK maintains many buildings and sites and wants to appeal to a corporate professional market with their brand new website. GK is essentially a handyman service offering all maintenance services to home owners, office managers, real estate agents and strata managers.

The Website:
We need a corporate website that appeals to our broader customer base (property owners, property managers, office managers) the copy is being written by a professional so use filler text for now.

Things that we want:
Home page that sets us apart and appeals to the corporate and residential market. The home page needs to not focus on either the residential or commercial market. The home page should focus on our logo and branding. We have a logo already and it is attached to the brief, please use it and try to consider the colour pallette that goes with it. Whilst we want the site to appear strong and manly it is important to remember that 95% of our customers are female so we need the site to be appealing to women. Women need to believe that we are strong, dependable and trustworthy.
We'd like a quote page and potentially also the ability to get a quote from the home page (please don't put it in if it ruins the overall feel of the home page)
An "about us" page
A contact us page
A blog that's built in (we don't want to link to an external blog)
(overall we'd expect to have 6 or 7 pages total)

The site will also need coding - we expect this to be done in a separate project but need you to consider a few things about the coding side of things.

It needs to be iPhone and iPad compatible.

We'd like you to suggest the best CMS that you would use or if you would suggest not using a CMS please let us know with your submissions.

Target Market(s)

Property owners, office managers and property managers who need maintenance on buildings (So all of them)

Industry/Entity Type

Property Maintenance

Requirements
Must have
• Our Logo
Home page
About Us
Residential
Commercial
Real Estate/Strata
Contact Us/Quote
Blog
Nice to have
• Quote form included in home page
Movement on the home page at least
Should not have
• other logos, too much colour
NO FLASH

```html
<!DOCTYPE html>
<html lang="en">
<head>
<meta charset="utf-8">
<title>Gold Kite handy man</title>
<link rel="stylesheet" href="https://fonts.googleapis.com/css2?family=Source+Sans+3:wght@400;600&display=swap">
<style>
:root{
  --orange:#f47f1f;
  --orange-deep:#e86d0d;
  --nav:#3a3a3a;
  --nav-active:#6b6b6b;
  --ink:#3c3c3c;
  --muted:#8a8a8a;
  --link:#9b1c1c;
  --foot:#353535;
  --foot-text:#e4e4e4;
  --gold:#f0b400;
}
*{box-sizing:border-box;margin:0;padding:0}
html,body{width:750px;height:1200px;overflow:hidden}
body{position:relative;background:#fff;font-family:"Source Sans 3",Arial,sans-serif;color:var(--ink)}
.abs{position:absolute}
.topbar{left:0;top:0;width:750px;height:19px;background:#f3f3f3;border-bottom:1px solid #e2e2e2}
.toplinks{right:20px;top:4px;font-size:8px;color:#666}
.toplinks span{padding:0 4px;border-left:1px solid #aaa}
.toplinks span:first-child{border:0}
.brand-mark{left:14px;top:21px;width:60px;height:60px;background:var(--orange)}
.brand-name{left:88px;top:33px;font-size:24px;color:#333;white-space:nowrap}
.phone{left:425px;top:39px;font-size:18px;color:#333;display:flex;align-items:center;gap:6px;white-space:nowrap}
.search-box{left:575px;top:39px;width:166px;height:23px;border:1px solid #bbb;border-radius:4px;background:#fafafa;font-size:8px;color:#999;padding:6px 0 0 18px}
.search-btn{right:2px;top:2px;width:28px;height:17px;background:var(--orange);border-radius:2px}
.nav{left:0;top:83px;width:750px;height:26px;background:var(--nav)}
.nav a{position:absolute;top:0;color:#fff;font-size:10px;text-decoration:none;line-height:26px;white-space:nowrap}
.nav a.active{left:17px;width:73px;text-align:center;background:var(--nav-active)}
.finder{left:0;top:109px;width:750px;height:75px;background:var(--orange)}
.finder-title{left:19px;top:28px;color:#fff;font-size:13px}
.radio{font-size:9px;color:#fff;display:flex;align-items:center;gap:8px;white-space:nowrap}
.radio i{width:8px;height:8px;border-radius:50%;background:#fff;display:inline-block}
.field-label{font-size:9px;color:#fff;text-align:right;width:70px;white-space:nowrap}
.field{width:131px;height:19px;background:#fff;border-radius:3px}
.finder-btn{left:637px;top:24px;width:92px;height:28px;background:linear-gradient(#333,#111);border-radius:3px;color:#fff;font-size:13px;text-align:center;line-height:28px;white-space:nowrap}
.slider{left:11px;top:196px;width:723px;height:279px;background:linear-gradient(90deg,#6f6a5f 0%,#9b3a2f 40%,#4e6b3a 60%,#7fa25b 100%)}
.slider-cap{left:0;bottom:0;width:100%;height:34px;background:rgba(60,60,60,.75);color:#f5b93a;font-size:9.5px;padding:12px 15px}
.arrow{top:120px;width:26px;height:28px;background:rgba(80,80,80,.75);color:#fff;font-size:11px;text-align:center;line-height:28px}
.welcome-title{left:16px;top:509px;color:var(--orange);font-size:14px;font-weight:400}
.welcome-text{left:19px;top:533px;width:382px;font-size:8.6px;line-height:15.8px}
.welcome-text p{margin-bottom:15.8px}
.view-more{left:336px;top:663px;font-size:8px;color:var(--link)}
.promo{left:411px;top:523px;width:331px;height:140px;background:linear-gradient(90deg,#e6eef5,#f7f7f7 55%,#d9c0a3)}
.projects{left:16px;top:706px;width:712px;height:239px;border:1px solid #bdbdbd;background:#fafafa}
.projects-title{left:20px;top:11px;font-size:12.5px;color:#333;font-weight:400}
.card{top:44px;width:143px}
.card-img{height:102px;border:1px solid #ccc}
.card-text{margin-top:12px;font-size:8.2px;line-height:14px;color:var(--muted)}
.card-more{margin-top:8px;margin-left:2px;font-size:8px;color:var(--link)}
.footer{left:0;top:962px;width:750px;height:238px;background:var(--foot);border-top:6px solid #222}
.foot-h{font-size:11px;color:var(--foot-text)}
.input{left:31px;width:134px;height:18px;background:linear-gradient(#f2f2f2,#d9d9d9);border-radius:4px;font-size:7.5px;color:#555;padding:5px 0 0 13px}
.comment{left:182px;top:1015px;width:134px;height:42px;background:linear-gradient(#f2f2f2,#d9d9d9);border-radius:3px;font-size:7.5px;color:#555;padding:14px 0 0 17px}
.submit{left:219px;top:1069px;width:82px;height:24px;border-radius:12px;background:linear-gradient(#ffc23a,#f08a00);border:1px solid #b86200;color:#fff;font-size:10px;font-weight:600;text-align:center;line-height:22px}
.thumb{left:407px;width:54px;height:49px;border:1px solid #888}
.blog-text{left:480px;width:236px;font-size:7.6px;line-height:10.5px;color:var(--foot-text)}
.blog-by{left:480px;font-size:7.6px;color:var(--foot-text)}
.foot-more{left:690px;top:1118px;font-size:8px;color:var(--gold)}
.foot-rule{left:170px;top:1140px;width:450px;height:1px;background:#555}
.social{top:1166px;width:17px;height:17px;border-radius:2px}
.copyright{right:16px;top:1163px;font-size:8px;color:var(--foot-text)}
</style>
</head>
<body>
<div class="abs topbar"></div>
<div class="abs toplinks"><span>New User</span><span>Register</span><span>Sign In</span><span>Help</span></div>

<div class="abs brand-mark" aria-hidden="true"></div>
<div class="abs brand-name">Gold Kite handy man</div>
<div class="abs phone">
  <svg width="18" height="20" viewBox="0 0 18 20"><path d="M4 1c1-.6 2 0 2.5 1l1.5 3.5c.4 1-.2 1.7-1 2.2l-1 .6c.8 2.3 2.2 4.3 4.2 5.8l.9-.8c.7-.6 1.6-.8 2.4-.2l3 2.2c.8.6.9 1.6.2 2.4l-1.3 1.4C13.5 21 4 15 1.5 6 1 4 2 2.3 4 1z" fill="#333"/></svg>
  200 555 018
</div>
<div class="abs search-box">Search
  <div class="abs search-btn"><svg width="28" height="17" viewBox="0 0 28 17"><circle cx="13" cy="7.5" r="3.2" fill="none" stroke="#fff" stroke-width="1.6"/><path d="M15.3 9.8l3 3" stroke="#fff" stroke-width="1.8"/></svg></div>
</div>

<nav class="abs nav">
  <a class="active">HOME</a>
  <a style="left:102px">ABOUT US</a>
  <a style="left:175px">RESIDENTIAL</a>
  <a style="left:260px">COMMERCIAL</a>
  <a style="left:349px">REAL ESTATE / STRATA</a>
  <a style="left:474px">CONTACT US</a>
  <a style="left:558px">QUOTE</a>
  <a style="left:620px">BLOG</a>
</nav>

<section class="abs finder" aria-label="Quick quote">
  <div class="abs finder-title">QUOTE</div>
  <div class="abs radio" style="left:97px;top:20px"><i style="box-shadow:inset 0 0 0 2px #fff,inset 0 0 0 4px var(--orange-deep)"></i>RESIDENTIAL</div>
  <div class="abs radio" style="left:97px;top:46px"><i></i>COMMERCIAL</div>
  <div class="abs field-label" style="left:195px;top:16px">Service Type</div>
  <div class="abs field" style="left:279px;top:11px"></div>
  <div class="abs field-label" style="left:195px;top:47px">Suburb</div>
  <div class="abs field" style="left:279px;top:43px"></div>
  <div class="abs field-label" style="left:413px;top:16px">Your Name</div>
  <div class="abs field" style="left:495px;top:12px"></div>
  <div class="abs field-label" style="left:413px;top:46px">Phone</div>
  <div class="abs field" style="left:495px;top:44px"></div>
  <div class="abs finder-btn">GET QUOTE</div>
</section>

<section class="abs slider" role="img" aria-label="Photo of a smiling woman in front of well kept townhouses">
  <div class="abs arrow" style="left:0">«</div>
  <div class="abs arrow" style="right:0">»</div>
  <div class="abs slider-cap">Ut blandit, turpis non interdum tincidunt, libero augue pretium libero, in vehicula quam.</div>
</section>

<h2 class="abs welcome-title">Welcome to GoldKitehandyman</h2>
<div class="abs welcome-text">
  <p>Lorem Ipsum is simply dummy text of the printing and typesetting industry. Lorem Ipsum has been the industry's standard dummy text ever since the 1500s, when an unknown printer took a galley of type and scrambled it to make a type specimen book.</p>
  <p>It has survived not only five centuries, but also the leap into electronic typesetting, remaining essentially unchanged. It was popularised in the 1960s with the release Lorem Ipsum has been the industry's standard dummy text ever since the 1500s, when an unknown printer took a galley of type and scrambled it to make a type specimen book.</p>
</div>
<div class="abs view-more">View More &gt;&gt;</div>
<div class="abs promo" role="img" aria-label="Illustrated banner of a freshly finished room with clouds and a smiling woman"></div>

<section class="abs projects">
  <h3 class="abs projects-title">RECENT PROJECTS</h3>
  <div class="abs card" style="left:14px"><div class="card-img" role="img" aria-label="Refurbished lounge with a dark sofa" style="background:linear-gradient(90deg,#c8842a 0 18%,#eee 18%,#ddd 60%,#444 60%)"></div><p class="card-text">Est omnis doloreserele dusempqui bdamet aurerum saepe eveniet utoluptates estu...</p><p class="card-more">Read More</p></div>
  <div class="abs card" style="left:187px"><div class="card-img" role="img" aria-label="Repainted living room with red furniture" style="background:linear-gradient(#eee 55%,#b53030 55%,#c9c9c9)"></div><p class="card-text">Est omnis doloreserele dusempqui bdamet aurerum saepe eveniet utoluptates estu...</p><p class="card-more">Read More</p></div>
  <div class="abs card" style="left:365px"><div class="card-img" role="img" aria-label="Lawn and garden maintenance at a family home" style="background:linear-gradient(#8a7a68 45%,#5f8a3a 45%)"></div><p class="card-text">Est omnis doloreserele dusempqui bdamet aurerum saepe eveniet utoluptates estu...</p><p class="card-more">Read More</p></div>
  <div class="abs card" style="left:545px"><div class="card-img" role="img" aria-label="Office fit-out with red chairs and a white table" style="background:linear-gradient(90deg,#ddd,#c9b86a 40%,#eee 60%,#b83a2e)"></div><p class="card-text">Est omnis doloreserele dusempqui bdamet aurerum saepe eveniet utoluptates estu...</p><p class="card-more">Read More</p></div>
</section>

<footer class="abs footer"></footer>
<div class="abs foot-h" style="left:31px;top:983px">CONTACT &nbsp;FORM</div>
<div class="abs input" style="top:1015px">User Name</div>
<div class="abs input" style="top:1045px">Password</div>
<div class="abs input" style="top:1076px">Phone Number</div>
<div class="abs comment">Comment</div>
<div class="abs submit">SUBMIT</div>

<div class="abs foot-h" style="left:407px;top:983px">BLOG</div>
<div class="abs thumb" style="top:1011px;background:linear-gradient(#9fb7c8,#c86a4a)" role="img" aria-label="Blog author portrait"></div>
<div class="abs blog-text" style="top:1010px">Nunc varius facilisis eros. Sed erat. In in velit quis arcu ornare laoreet. luctus massa.Nunc varius facilisis eros. Sed erat. In in velit quis arcu ornare laoreet. luctus massa.</div>
<div class="abs blog-by" style="top:1051px">By Jenna at &nbsp;Fri 12:01 PM</div>
<div class="abs thumb" style="top:1073px;background:linear-gradient(#8a8f7a,#5a4a3a)" role="img" aria-label="Blog author portrait"></div>
<div class="abs blog-text" style="top:1069px">Nunc varius facilisis eros. Sed erat. In in velit quis arcu ornare laoreet. luctus massa.Nunc varius facilisis eros. Sed erat. In in velit quis arcu ornare laoreet. luctus massa.</div>
<div class="abs blog-by" style="top:1110px">By Jenna at &nbsp;Fri 12:01 PM</div>
<div class="abs foot-more">Read More</div>
<div class="abs foot-rule"></div>

<div class="abs social" style="left:33px;background:#3b5b9a"></div>
<div class="abs social" style="left:63px;background:#4fb3e0"></div>
<div class="abs social" style="left:93px;background:#e8702a"></div>
<div class="abs social" style="left:123px;background:#2a7ab0"></div>
<div class="abs social" style="left:153px;background:#d9d9d9"></div>
<div class="abs copyright">Copyright © 2012 .goldkitehandyman.example.au,All rights reserved</div>
</body>
</html>
```